Redesign of business card for Cedar Ridge Mechanical

We are looking for a new design for our business cards for Cedar Ridge Mechanical. We are a plumbing & HVAC construction company, operating on the West Coast of Canada and USA. Logo attached.
Industry/Entity Type
Construction - Plumbing & HVAC
Contact Information for Business Card
Name, address, phone numbers, email, website address
Look and feel
Each slider illustrates characteristics of the customer's brand and the style your logo design should communicate.

```html
<!DOCTYPE html>
<html lang="en">
<head>
<meta charset="utf-8">
<title>Cedar Ridge Mechanical – Business Card</title>
<link rel="stylesheet" href="https://fonts.googleapis.com/css2?family=Montserrat:wght@400;700&display=swap">
<style>
  :root {
    --stage: #3b3b3b;
    --card-white: #ffffff;
    --ink: #111111;
    --ink-soft: #333333;
    --shadow: rgba(0, 0, 0, 0.45);
  }
  * { box-sizing: border-box; margin: 0; padding: 0; }
  html, body {
    width: 1200px; height: 689px; overflow: hidden;
    background: var(--stage);
    font-family: "Montserrat", sans-serif;
    color: var(--ink);
  }
  .stage {
    position: relative; width: 1200px; height: 689px;
    display: flex; align-items: center; justify-content: center; gap: 40px;
  }
  .card {
    position: relative; width: 540px; height: 309px;
    border-radius: 22px; overflow: hidden;
    box-shadow: 0 14px 34px var(--shadow);
  }

  /* Front */
  .card--front {
    background: var(--card-white);
    display: flex; align-items: center; justify-content: center; gap: 14px;
  }
  .brand-mark {
    width: 26px; height: 26px; background: var(--ink); flex: none;
  }
  .brand-name {
    font-weight: 700; font-size: 30px; letter-spacing: 0.5px;
    line-height: 1.1; text-transform: uppercase; color: var(--ink);
  }

  /* Back */
  .card--back { background: var(--ink); }
  .back-panel {
    position: absolute; left: 78px; top: -160px;
    width: 444px; height: 630px; border-radius: 50%;
    background: var(--card-white);
  }
  .back-content {
    position: absolute; inset: 0;
    display: grid; grid-template-columns: 168px 1px 1fr;
    grid-template-rows: 1fr auto; column-gap: 18px;
    padding: 52px 62px 36px 102px;
  }
  .back-brand {
    display: flex; align-items: center; gap: 9px;
  }
  .back-brand .brand-mark { width: 15px; height: 15px; }
  .back-brand .brand-name { font-size: 15px; }
  .divider { background: var(--ink); width: 1px; height: 140px; align-self: center; }
  .contact { align-self: center; }
  .person-name { font-weight: 700; font-size: 17px; letter-spacing: 0.5px; white-space: nowrap; }
  .person-role { font-size: 11px; color: var(--ink-soft); margin-bottom: 12px; }
  .contact-list { list-style: none; font-size: 11px; }
  .contact-list li { display: flex; align-items: center; gap: 7px; margin-bottom: 5px; white-space: nowrap; }
  .contact-list svg { width: 10px; height: 10px; fill: var(--ink); flex: none; }
  .address {
    grid-column: 1 / -1; text-align: right; font-size: 11px; white-space: nowrap;
  }
</style>
</head>
<body>
<main class="stage">
  <section class="card card--front" aria-label="Card front">
    <span class="brand-mark" aria-hidden="true"></span>
    <span class="brand-name">Cedar Ridge<br>Mechanical</span>
  </section>

  <section class="card card--back" aria-label="Card back">
    <div class="back-panel" aria-hidden="true"></div>
    <div class="back-content">
      <div class="back-brand">
        <span class="brand-mark" aria-hidden="true"></span>
        <span class="brand-name">Cedar Ridge<br>Mechanical</span>
      </div>
      <div class="divider" aria-hidden="true"></div>
      <div class="contact">
        <p class="person-name">DANIEL HAYES</p>
        <p class="person-role">Managing Director</p>
        <ul class="contact-list">
          <li><svg viewBox="0 0 10 10"><path d="M2 0.5 3.8 2.6 2.9 3.7a6 6 0 0 0 3.4 3.4l1.1-.9 2.1 1.8-1 1.5C4.4 9.4.6 5.6.5 1.5z"/></svg>123 456 789</li>
          <li><svg viewBox="0 0 10 10"><path d="M0 2h10v6H0zM.8 2.6 5 5.6l4.2-3H.8z"/></svg>info@yourgmail.com</li>
          <li><svg viewBox="0 0 10 10"><circle cx="5" cy="5" r="4.5"/></svg>www.yourwebsite.com</li>
        </ul>
      </div>
      <p class="address">Your address, City State, Zip 1234</p>
    </div>
  </section>
</main>
</body>
</html>
```